VENTURE CAPITAL GROUP BUSINESS CARD DESIGN

Venture Capital Group based in SF looking for a bold business card design. No trendy colour explosion, 3D effects etc. Just "simple" optical effects. Works on your brain, keeps your eye focused and sticks to your mind.
Target Market(s)
Technology startups
Industry/Entity Type
Venture Capital
Contact Information for Business Card
DESMOND WHITLAKE
MANAGING PARTNER
187 FENWORTH ST SAN FRANCISCO, CA 94187
415.555.0142 O
415.555.0147 F
415.555.0193 C
desmond@veldtmoorcapital.ventures

```html
<!DOCTYPE html>
<html lang="en">
<head>
<meta charset="utf-8">
<title>Veldtmoor Capital Group – Business Card</title>
<link href="https://fonts.googleapis.com/css2?family=Open+Sans:wght@400;600;700&display=swap" rel="stylesheet">
<style>
  :root {
    --stage: #000000;
    --paper: #ffffff;
    --ink: #1a1a1a;
    --brand-green: #1f7a2e;
    --icon-green: #2e8b3a;
    --back-dark: #0f5a1f;
    --back-mid: #2f8f3c;
    --back-light: #58b857;
    --seal-light: #f4f4f4;
    --seal-shade: #d6d6d6;
  }
  html, body {
    margin: 0;
    width: 1200px;
    height: 900px;
    overflow: hidden;
    background: var(--stage);
    font-family: "Open Sans", Arial, sans-serif;
  }
  .stage { position: relative; width: 1200px; height: 900px; }

  .card { position: absolute; top: 275px; width: 477px; height: 293px; overflow: hidden; }

  .card-front {
    left: 116px;
    background: var(--paper);
    border-radius: 0 52px 0 52px;
    color: var(--ink);
  }
  .card-back {
    left: 622px;
    top: 276px;
    height: 292px;
    border-radius: 52px 0 52px 0;
    background:
      radial-gradient(ellipse 70% 90% at 95% 0%, var(--back-light) 0%, rgba(88,184,87,0) 70%),
      linear-gradient(125deg, var(--back-dark) 0%, var(--back-mid) 55%, var(--back-light) 100%);
  }
  .back-sweep {
    position: absolute;
    left: 0; top: 0;
    width: 230px; height: 292px;
    background: radial-gradient(ellipse 100% 60% at 0% 45%, rgba(10,70,25,0.55) 0%, rgba(10,70,25,0) 75%);
  }

  .brand-seal {
    position: absolute;
    left: 84px; top: 53px;
    width: 90px; height: 90px;
    border-radius: 50%;
    background: radial-gradient(circle at 40% 35%, var(--seal-light) 0%, var(--seal-shade) 100%);
  }
  .brand-name {
    position: absolute;
    left: 34px; top: 156px;
    width: 190px;
    text-align: center;
    color: var(--brand-green);
    font-weight: 600;
    line-height: 1;
  }
  .brand-name .word { display: block; font-size: 27px; letter-spacing: 0.5px; }
  .brand-name .sub { display: block; font-size: 8.5px; letter-spacing: 3.2px; margin-top: 4px; text-transform: uppercase; }

  .identity { position: absolute; right: 27px; top: 29px; text-align: right; }
  .person-name { margin: 0; font-size: 17px; font-weight: 700; color: var(--brand-green); line-height: 1.2; }
  .person-title { margin: 2px 0 0; font-size: 12.5px; }

  .contact-list {
    position: absolute;
    right: 27px; top: 160px;
    margin: 0; padding: 0; list-style: none;
    text-align: right;
    font-size: 12.5px;
    line-height: 19.7px;
  }
  .contact-list li { display: flex; justify-content: flex-end; align-items: center; gap: 4px; }
  .contact-list svg { width: 9px; height: 9px; fill: var(--icon-green); flex: none; }
  .contact-list .address { margin-top: 3px; }

  .back-name {
    position: absolute;
    right: 40px; top: 222px;
    color: #ffffff;
    text-align: center;
    font-weight: 600;
    line-height: 1;
  }
  .back-name .word { display: block; font-size: 33px; letter-spacing: 0.5px; }
  .back-name .sub { display: block; font-size: 10px; letter-spacing: 4px; margin-top: 4px; text-transform: uppercase; }
</style>
</head>
<body>
<main class="stage">

  <section class="card card-front" aria-label="Card front">
    <div class="brand-seal" aria-hidden="true"></div>
    <div class="brand-name">
      <span class="word">VELDTMOOR</span>
      <span class="sub">Capital Group</span>
    </div>

    <div class="identity">
      <p class="person-name">Desmond Whitlake</p>
      <p class="person-title">Managing Partner</p>
    </div>

    <ul class="contact-list">
      <li>415.555.0142
        <svg viewBox="0 0 10 10" aria-label="Office"><path d="M2 0.5 L3.8 2.6 L2.9 3.8 C3.6 5.2 4.8 6.4 6.2 7.1 L7.4 6.2 L9.5 8 L8.3 9.5 C4.4 9.2 0.8 5.6 0.5 1.7 Z"/></svg>
      </li>
      <li>415.555.0147
        <svg viewBox="0 0 10 10" aria-label="Fax"><path d="M2.5 0.5 H7.5 V3 H9.5 V9.5 H0.5 V3 H2.5 Z M3.3 1.3 V3 H6.7 V1.3 Z M2 5 V6 H8 V5 Z M2 7 V8 H8 V7 Z" fill-rule="evenodd"/></svg>
      </li>
      <li>415.555.0193
        <svg viewBox="0 0 10 10" aria-label="Mobile"><path d="M2.5 0 H7.5 V10 H2.5 Z M3.3 1 V8 H6.7 V1 Z" fill-rule="evenodd"/></svg>
      </li>
      <li>desmond@veldtmoorcapital.ventures
        <svg viewBox="0 0 10 10" aria-label="Email"><path d="M0.5 2 H9.5 V8 H0.5 Z M1.2 2.6 L5 5.4 L8.8 2.6 Z" fill-rule="evenodd"/></svg>
      </li>
      <li class="address">187 Fenworth St San Francisco, CA 94187</li>
    </ul>
  </section>

  <section class="card card-back" aria-label="Card back">
    <div class="back-sweep" role="img" aria-label="Soft dark green sweep decoration"></div>
    <div class="back-name">
      <span class="word">VELDTMOOR</span>
      <span class="sub">Capital Group</span>
    </div>
  </section>

</main>
</body>
</html>
```